ALL TYPES OF COMMERCIAL PLASTERING

TYPE OF BLOCK LETTERING WITH STAND OUT QUALITIES
WITH SOME TYPE OF LOGO
SOMETHING UNIQUE FOR THE BUILDING INDUSTRY.
QUALITY WORKMANSHIP
Updates

forgot to include my mobile phone number on my brief. could you add it to your design please MOBILE PH 0491 586 032

please let me make this quite clear ,the company name is harbourline linings and Fitouts PTY LTD. THE TYPE OF WORK WE WILL BE DOING IS COMMERCIAL PLASTERING.

Industry/Entity Type

Industry

Contact Information for Business Card

harbourline linings and fitouts P/L
marcus trelawny p.o.box 82 wendouree 3355 email address harbourlinelinings@mailcove.example
ABN 84 519 263 740 COMMERCIAL PLASTERING

```html
<!DOCTYPE html>
<html lang="en">
<head>
<meta charset="utf-8">
<title>harbourline linings and fitouts P/L — business card</title>
<link href="https://fonts.googleapis.com/css2?family=Arimo:wght@400;700&display=swap" rel="stylesheet">
<style>
  :root {
    --backdrop: #e9e6e1;
    --card: #ffffff;
    --ink: #111111;
    --brand: #9a4aa3;
    --brand-soft: #e6d3e9;
  }
  html, body {
    margin: 0;
    padding: 0;
    width: 1200px;
    height: 800px;
    overflow: hidden;
    background: var(--backdrop);
    font-family: "Arimo", Arial, sans-serif;
  }
  .card {
    position: absolute;
    left: 100px;
    top: 114px;
    width: 1000px;
    height: 572px;
    background: var(--card);
    box-shadow: 0 10px 30px rgba(0,0,0,0.18);
    overflow: hidden;
  }
  .brand {
    position: absolute;
    left: 70px;
    top: 52px;
    display: flex;
    align-items: center;
    gap: 26px;
  }
  .brand-mark {
    width: 130px;
    height: 130px;
    border-radius: 50%;
    background: var(--brand-soft);
    flex: none;
  }
  .brand-name {
    color: var(--brand);
    font-weight: 700;
    font-size: 40px;
    line-height: 1.05;
    text-transform: uppercase;
    letter-spacing: 1px;
  }
  .brand-trade {
    margin-top: 10px;
    color: var(--ink);
    font-size: 17px;
    letter-spacing: 1px;
    text-transform: uppercase;
  }
  .person {
    position: absolute;
    left: 70px;
    top: 236px;
    margin: 0;
    font-size: 44px;
    font-weight: 400;
    color: var(--ink);
  }
  .contacts {
    position: absolute;
    left: 70px;
    top: 320px;
    margin: 0;
    padding: 0;
    list-style: none;
    font-size: 25px;
    color: var(--ink);
  }
  .contacts li {
    display: flex;
    align-items: center;
    gap: 18px;
    height: 40px;
  }
  .contacts svg {
    width: 24px;
    height: 24px;
    fill: var(--brand);
    flex: none;
  }
  .accent-band {
    position: absolute;
    right: 0;
    bottom: 0;
    width: 62%;
    height: 42px;
    background: var(--brand);
  }
</style>
</head>
<body>
  <main class="card">
    <header class="brand">
      <div class="brand-mark"></div>
      <div>
        <div class="brand-name">harbourline linings<br>and fitouts P/L</div>
        <div class="brand-trade">commercial plastering</div>
      </div>
    </header>

    <h1 class="person">marcus trelawny</h1>

    <ul class="contacts">
      <li>
        <svg viewBox="0 0 24 24" aria-hidden="true"><path d="M7 1h10a2 2 0 0 1 2 2v18a2 2 0 0 1-2 2H7a2 2 0 0 1-2-2V3a2 2 0 0 1 2-2zm0 3v12h10V4zm5 14.5a1.5 1.5 0 1 0 0 3 1.5 1.5 0 0 0 0-3z"/></svg>
        0491 586 032
      </li>
      <li>
        <svg viewBox="0 0 24 24" aria-hidden="true"><path d="M12 1a8 8 0 0 0-8 8c0 6 8 14 8 14s8-8 8-14a8 8 0 0 0-8-8zm0 11a3 3 0 1 1 0-6 3 3 0 0 1 0 6z"/></svg>
        ABN 84 519 263 740
      </li>
      <li>
        <svg viewBox="0 0 24 24" aria-hidden="true"><path d="M12 2 1 12h3v10h6v-6h4v6h6V12h3z"/></svg>
        p.o.box 82 wendouree 3355
      </li>
      <li>
        <svg viewBox="0 0 24 24" aria-hidden="true"><path d="M2 5h20v14H2zm2 2v.5l8 5.5 8-5.5V7zm0 3v7h16v-7l-8 5.5z"/></svg>
        harbourlinelinings@mailcove.example
      </li>
    </ul>

    <div class="accent-band"></div>
  </main>
</body>
</html>
```